Building technology company seek stationery design and folder design

Letterhead, and a folder design
ideally, I would have two letter head design, one is for one-page bussiness letter. the other one I can use for longer document such report, or analysis regular report page
you can find company logo and overall style at our website:
www.structavolt.example

we are in building technology business, using internet of things technology to improve building energy efficiency to make building greener.

Industry/Entity Type

It Company

Requirements
Must have
• company logo
Nice to have
• techy look abstract graphics, etc.
Should not have
• no comment

```html
<!DOCTYPE html>
<html lang="en">
<head>
<meta charset="utf-8">
<title>Structavolt Letterhead</title>
<link href="https://fonts.googleapis.com/css2?family=Roboto:wght@400;500&display=swap" rel="stylesheet">
<style>
  :root {
    --backdrop: #5c5b68;
    --paper: #ffffff;
    --header-dark: #0a1c20;
    --accent-green: #a3cc2a;
    --contact-text: #ffffff;
    --skyline-grey: #f1f1ef;
  }
  html, body {
    margin: 0;
    padding: 0;
    width: 1200px;
    height: 992px;
    overflow: hidden;
    background: var(--backdrop);
    font-family: "Roboto", Arial, sans-serif;
  }
  .letterhead {
    position: absolute;
    left: 250px;
    top: 23px;
    width: 700px;
    height: 946px;
    background: var(--paper);
    box-shadow: 0 10px 30px rgba(0,0,0,0.35);
    overflow: hidden;
  }
  .letterhead__header {
    position: absolute;
    left: 0; top: 0;
    width: 100%;
    height: 108px;
    background: var(--header-dark);
    border-bottom: 5px solid var(--accent-green);
  }
  .brand {
    position: absolute;
    left: 56px;
    top: 42px;
    display: flex;
    align-items: center;
    gap: 10px;
  }
  .brand__square {
    width: 22px;
    height: 22px;
    background: var(--accent-green);
  }
  .brand__name {
    font-size: 24px;
    font-weight: 500;
    letter-spacing: 3px;
    color: var(--accent-green);
  }
  .contact {
    position: absolute;
    left: 522px;
    top: 32px;
    margin: 0;
    padding: 0;
    list-style: none;
  }
  .contact__item {
    display: flex;
    align-items: center;
    gap: 5px;
    height: 15.5px;
    font-size: 11px;
    color: var(--contact-text);
  }
  .contact__icon {
    width: 10px;
    height: 10px;
    flex: none;
  }
  .skyline-band {
    position: absolute;
    left: 0;
    bottom: 0;
    width: 100%;
    height: 142px;
    background: linear-gradient(to bottom, rgba(241,241,239,0.6), var(--skyline-grey) 25%);
  }
</style>
</head>
<body>
  <div class="letterhead">
    <header class="letterhead__header">
      <div class="brand">
        <span class="brand__square"></span>
        <span class="brand__name">STRUCTAVOLT</span>
      </div>
      <ul class="contact">
        <li class="contact__item">
          <svg class="contact__icon" viewBox="0 0 10 10"><path d="M2 0.8 L3.6 2.6 L2.8 3.7 Q3.8 5.9 6.1 7.1 L7.2 6.2 L9.2 7.8 L8.2 9.3 Q4.5 9.4 1.8 6.6 Q0.4 4.4 0.6 1.8 Z" fill="var(--accent-green)"/></svg>
          (555) 014-2280
        </li>
        <li class="contact__item">
          <svg class="contact__icon" viewBox="0 0 10 10"><rect x="0.5" y="2" width="9" height="6.5" fill="var(--accent-green)"/><path d="M0.5 2 L5 5.6 L9.5 2" stroke="var(--header-dark)" stroke-width="0.9" fill="none"/></svg>
          info@structavolt.example
        </li>
        <li class="contact__item">
          <svg class="contact__icon" viewBox="0 0 10 10" fill="none" stroke="var(--accent-green)" stroke-width="0.9"><circle cx="5" cy="5" r="4.2"/><ellipse cx="5" cy="5" rx="1.8" ry="4.2"/><line x1="0.8" y1="5" x2="9.2" y2="5"/></svg>
          www.structavolt.example
        </li>
      </ul>
    </header>
    <div class="skyline-band" role="img" aria-label="Faint light grey city skyline silhouette along the bottom edge"></div>
  </div>
</body>
</html>
```